Medical VIP club - small design

Please read the specs in a design brief attached. Also we don't have logo in a Vector format and attaching the only version we have.

Club

```html
<!DOCTYPE html>
<html lang="en">
<head>
<meta charset="utf-8">
<title>Curanta VIP Medical Club</title>
<link rel="stylesheet" href="https://fonts.googleapis.com/css2?family=Roboto+Condensed:wght@400;700&display=swap">
<style>
:root{
  --bg-dark:#5a4938;
  --bg-mid:#8a7c6c;
  --bg-light:#cfcac2;
  --cream:#f7f4e6;
  --cream-deep:#e7e2cc;
  --tab-text:#4a3a2a;
  --accent:#8c2a0c;
  --brown:#5b4630;
  --card-text:#4e3d2c;
  --well-dark:#6d6a60;
  --well-light:#b9b6ab;
  --link:#f1ece0;
}
*{box-sizing:border-box;margin:0;padding:0}
html,body{width:1200px;height:900px;overflow:hidden}
body{
  position:relative;
  font-family:"Roboto Condensed",sans-serif;
  background:linear-gradient(180deg,var(--bg-dark) 0%,var(--bg-dark) 14%,var(--bg-mid) 30%,var(--bg-light) 48%,var(--bg-mid) 64%,var(--bg-dark) 80%,var(--bg-dark) 100%);
}
.brand{
  position:absolute;left:160px;top:40px;
  display:flex;align-items:center;gap:12px;
}
.brand-mark{width:36px;height:36px;border-radius:50%;background:var(--cream-deep)}
.brand-name{font-size:58px;font-weight:700;color:var(--cream-deep);letter-spacing:1px;line-height:1}
.site{
  position:absolute;left:127px;top:137px;width:946px;height:704px;
  border-radius:26px;overflow:hidden;
  box-shadow:0 4px 10px rgba(0,0,0,.35);
}
.nav{
  display:flex;height:74px;
  background:linear-gradient(180deg,#fffdf2 0%,var(--cream) 55%,var(--cream-deep) 100%);
}
.nav-tab{
  flex:1;display:flex;align-items:center;justify-content:center;
  padding-top:10px;
  font-size:19px;color:var(--tab-text);text-decoration:none;letter-spacing:-.3px;
  border-left:1px solid #c9c2a8;border-top-left-radius:28px;
  box-shadow:inset 2px 3px 4px rgba(255,255,255,.9);
}
.nav-tab:first-child{border-left:none}
.nav-tab.is-cta{color:var(--accent);font-weight:700}
.content{
  position:relative;height:551px;
  background:linear-gradient(180deg,var(--well-dark) 0%,var(--well-light) 35%,#d8d5cb 60%,var(--well-light) 85%,#8f8b80 100%);
  box-shadow:inset 0 6px 8px rgba(0,0,0,.3);
}
.card{
  position:absolute;left:30px;width:866px;height:144px;
  border-radius:12px;overflow:hidden;display:flex;
  background:linear-gradient(180deg,#f3f0e1 0%,#e6e1cb 100%);
  box-shadow:0 3px 6px rgba(0,0,0,.3);
}
.card:nth-of-type(1){top:37px}
.card:nth-of-type(2){top:205px}
.card:nth-of-type(3){top:373px}
.card-media{width:190px;flex:none;border-right:3px solid #b9a57c;border-top-right-radius:34px}
.media-clinic{background:linear-gradient(135deg,#3c5f9c 0%,#2a2a2e 60%,#5a5a5a 100%)}
.media-doctors{background:linear-gradient(180deg,#e6eef4 0%,#b9cbd8 60%,#8fb3c0 100%)}
.media-flight{background:linear-gradient(180deg,#2c5fa8 0%,#7ea6d4 60%,#e9cf8c 100%)}
.card-body{padding:24px 30px 0 26px}
.card-title{font-size:20px;font-weight:700;color:var(--brown);line-height:1.2;margin-bottom:2px}
.card-text{font-size:14px;line-height:19px;color:var(--card-text)}
.scrollbar{
  position:absolute;right:4px;top:6px;width:22px;height:540px;
}
.scroll-track{position:absolute;left:2px;top:0;width:18px;height:430px;border-radius:9px;background:linear-gradient(90deg,#d9ceb0,#fffbe8,#c8b98f);box-shadow:inset 0 0 2px #5a4a30}
.scroll-thumb{position:absolute;left:5px;top:4px;width:12px;height:420px;border-radius:6px;background:linear-gradient(90deg,#7a5f3e,#a08461,#6b5236)}
.scroll-btn{position:absolute;left:0;width:22px;height:18px;background:#d5c9a8;border:1px solid #a89870}
.scroll-btn.up{bottom:20px}
.scroll-btn.down{bottom:0}
.footer{
  height:79px;display:flex;align-items:center;justify-content:center;gap:14px;
  background:linear-gradient(180deg,#fffdf2 0%,var(--cream) 50%,var(--cream-deep) 100%);
}
.follow{font-size:13px;color:var(--tab-text);margin-right:2px}
.social{width:36px;height:36px;border-radius:6px;display:block}
.social-a{background:#8fd0ec}
.social-b{background:#e2742e}
.social-c{background:#3b5a9a}
.bottom-links{
  position:absolute;top:850px;left:0;width:1200px;
  display:flex;justify-content:center;gap:18px;
  font-size:15px;color:var(--link);
}
.bottom-links a{color:inherit;text-decoration:none}
.bottom-links .sep{color:var(--link)}
</style>
</head>
<body>
<div class="brand">
  <span class="brand-mark"></span>
  <span class="brand-name">Curanta</span>
</div>

<div class="site">
  <nav class="nav">
    <a class="nav-tab" href="#">About us</a>
    <a class="nav-tab" href="#">VIP Club</a>
    <a class="nav-tab" href="#">Services</a>
    <a class="nav-tab" href="#">Packages @ Prices</a>
    <a class="nav-tab" href="#">Contacs</a>
    <a class="nav-tab is-cta" href="#">Registration</a>
  </nav>

  <main class="content">
    <article class="card">
      <div class="card-media media-clinic" role="img" aria-label="Hospital direction signs for emergency, parking and clinics"></div>
      <div class="card-body">
        <h2 class="card-title">Hospital will arrange your schedule and kok dndln</h2>
        <p class="card-text">Our coordinators plan every appointment, test and consultation in advance so that you spend your time on treatment rather than waiting. We book rooms, arrange translators and confirm each visit with the hospital departments. You receive a clear daily plan before arrival, and any change is handled by your personal manager at once, with updates sent to you directly.</p>
      </div>
    </article>
    <article class="card">
      <div class="card-media media-doctors" role="img" aria-label="Team of doctors and nurses in a clinic"></div>
      <div class="card-body">
        <h2 class="card-title">We provide you excellent doctors to and kok dnd</h2>
        <p class="card-text">Our network includes leading specialists in cardiology, oncology, orthopedics and neurology, each with long clinical experience. We match you with the right doctor after reviewing your records, so the first meeting is focused and useful. Second opinions, follow-up care and remote consultations are arranged through the club whenever you need them.</p>
      </div>
    </article>
    <article class="card">
      <div class="card-media media-flight" role="img" aria-label="Passenger airplane flying in a blue sky"></div>
      <div class="card-body">
        <h2 class="card-title">Every time is important, thats why we</h2>
        <p class="card-text">Flights, airport transfers and hotel stays are booked together with your medical plan, so nothing overlaps. A driver meets you on arrival and brings you to each appointment on time. Our team stays in touch throughout the trip and helps with the return journey and any documents you need afterwards.</p>
      </div>
    </article>

    <div class="scrollbar">
      <div class="scroll-track"><div class="scroll-thumb"></div></div>
      <span class="scroll-btn up"><svg width="20" height="16" viewBox="0 0 20 16"><path d="M6 11 L10 5 L14 11 Z" fill="#6b5a3a"/></svg></span>
      <span class="scroll-btn down"><svg width="20" height="16" viewBox="0 0 20 16"><path d="M6 5 L14 5 L10 11 Z" fill="#6b5a3a"/></svg></span>
    </div>
  </main>

  <footer class="footer">
    <span class="follow">Follow us on</span>
    <a class="social social-a" href="#" aria-label="Social network one"></a>
    <a class="social social-b" href="#" aria-label="News feed"></a>
    <a class="social social-c" href="#" aria-label="Social network two"></a>
  </footer>
</div>

<nav class="bottom-links">
  <a href="#">Home</a><span class="sep">I</span>
  <a href="#">Services</a><span class="sep">I</span>
  <a href="#">About us</a><span class="sep">I</span>
  <a href="#">Contact us</a>
</nav>
</body>
</html>
```